Velmarotix - world unique technology for better life - please let them know who am i at first sight

We need a new business card for company which is a provider of unique crystal based technology suitable for all living being. For more information and final design you can use our brochure (our colours are black and blue from brochure).
We use Verdana font

Industry/Entity Type

Business

Contact Information for Business Card

regular dimension

Font styles to use
Other font styles liked:
• Verdana

Requirements
Must have
• Logo
• name
• function/position
• phone
• mobile
• e-mail
• adress
Nice to have
• inovative design (technology directed)

```html
<!DOCTYPE html>
<html lang="en">
<head>
<meta charset="utf-8">
<title>Velmarotix – Business Card</title>
<link rel="stylesheet" href="https://fonts.googleapis.com/css2?family=Open+Sans:wght@400;700&display=swap">
<style>
  :root {
    --brand-blue: #29a8e0;
    --panel-white: #ffffff;
    --panel-shade: #e9eaec;
    --edge-grey: #a5a7aa;
    --page-bg: #eceef0;
    --text-light: #ffffff;
  }
  * { margin: 0; padding: 0; box-sizing: border-box; }
  html, body {
    width: 1200px;
    height: 900px;
    overflow: hidden;
    background: var(--page-bg);
    font-family: "Open Sans", Verdana, sans-serif;
  }
  .business-card {
    position: absolute;
    left: 100px;
    top: 165px;
    width: 1000px;
    height: 570px;
    border-radius: 44px;
    overflow: hidden;
    box-shadow: 0 18px 40px rgba(0, 0, 0, 0.18);
  }
  .card-shapes {
    position: absolute;
    inset: 0;
  }
  .holder {
    position: absolute;
    left: 58px;
    top: 118px;
    color: var(--text-light);
  }
  .holder-name {
    font-size: 32px;
    font-weight: 700;
    line-height: 1.1;
  }
  .holder-role {
    font-size: 27px;
    font-weight: 400;
    line-height: 1.15;
  }
  .address {
    position: absolute;
    left: 92px;
    top: 262px;
    color: var(--text-light);
    font-size: 23px;
    line-height: 1.35;
    font-style: normal;
  }
  .contact-list {
    position: absolute;
    left: 118px;
    top: 388px;
    list-style: none;
    color: var(--text-light);
    font-size: 22px;
    line-height: 1.32;
  }
  .contact-item {
    display: flex;
    align-items: center;
    gap: 14px;
  }
  .contact-icon {
    width: 19px;
    height: 19px;
    flex: none;
  }
  .brand-mark {
    position: absolute;
    left: 585px;
    top: 242px;
    display: flex;
    align-items: center;
    gap: 18px;
  }
  .brand-dot {
    width: 80px;
    height: 80px;
    border-radius: 50%;
    background: var(--brand-blue);
  }
  .brand-name {
    font-size: 50px;
    font-weight: 400;
    color: var(--brand-blue);
    letter-spacing: 1px;
  }
</style>
</head>
<body>
  <article class="business-card">
    <svg class="card-shapes" width="1000" height="570" viewBox="0 0 1000 570" aria-hidden="true">
      <defs>
        <linearGradient id="panel-fill" x1="0" y1="0" x2="0.6" y2="1">
          <stop offset="0" stop-color="#ffffff"/>
          <stop offset="1" stop-color="#e9eaec"/>
        </linearGradient>
      </defs>
      <rect class="blue-field" width="1000" height="570" fill="var(--brand-blue)"/>
      <path class="grey-edge" d="M400,0 C330,180 350,430 530,570 L1000,570 L1000,0 Z" fill="var(--edge-grey)"/>
      <path class="white-panel" d="M430,0 C360,170 380,420 600,570 L1000,570 L1000,0 Z" fill="url(#panel-fill)"/>
    </svg>

    <header class="holder">
      <h1 class="holder-name">Daniel Verhovec</h1>
      <p class="holder-role">Director</p>
    </header>

    <address class="address">
      27.14th floor,Plaza<br>
      Harwell Road NTV
    </address>

    <ul class="contact-list">
      <li class="contact-item">
        <svg class="contact-icon" viewBox="0 0 20 20" aria-label="Mobile"><rect x="5" y="1" width="10" height="18" rx="2" fill="none" stroke="#fff" stroke-width="2"/><circle cx="10" cy="15.5" r="1.2" fill="#fff"/></svg>
        <span>021 480 3157</span>
      </li>
      <li class="contact-item">
        <svg class="contact-icon" viewBox="0 0 20 20" aria-label="Phone"><path d="M4 2 L8 2 L9 6 L7 8 C8 11 9 12 12 13 L14 11 L18 12 L18 16 C18 17 17 18 16 18 C8 18 2 12 2 4 C2 3 3 2 4 2 Z" fill="#fff"/></svg>
        <span>021 480 3158</span>
      </li>
      <li class="contact-item">
        <svg class="contact-icon" viewBox="0 0 20 20" aria-label="Email"><rect x="1" y="4" width="18" height="12" fill="#fff"/><path d="M1 4 L10 11 L19 4" fill="none" stroke="#29a8e0" stroke-width="1.6"/></svg>
        <span>info@velmarotix.com</span>
      </li>
      <li class="contact-item">
        <svg class="contact-icon" viewBox="0 0 20 20" aria-label="Website"><circle cx="10" cy="10" r="8.5" fill="none" stroke="#fff" stroke-width="1.8"/><ellipse cx="10" cy="10" rx="3.5" ry="8.5" fill="none" stroke="#fff" stroke-width="1.5"/><path d="M1.5 10 H18.5 M3 5.5 H17 M3 14.5 H17" stroke="#fff" stroke-width="1.4"/></svg>
        <span>www.velmarotix.com</span>
      </li>
    </ul>

    <div class="brand-mark">
      <span class="brand-dot"></span>
      <span class="brand-name">Velmarotix</span>
    </div>
  </article>
</body>
</html>
```